RW Framewell Inc Business cards

We need business cards using our existing logo but slightly modified. Right now the logo says RW Loadbearing Masonry. We want to keep the RW part of the design, but replace the Structural Concrete portion with "FRAMEWELL". Please see the attached file.
Ideally this would be a blank template so we can add Different Names, titles, and phone numbers later.
On the one side we want only the logo and on the other side the detail. I'm attaching an example for you to see.
Please reach out with any other questions. Our address and other details will be given out once we find a design we like.

Target Market(s)

Construction Industry

```html
<!DOCTYPE html>
<html lang="en">
<head>
<meta charset="utf-8">
<title>RW Framewell Inc Business Cards</title>
<link href="https://fonts.googleapis.com/css2?family=Exo+2:wght@600&family=Roboto:wght@400;700&family=Roboto+Condensed:wght@500&display=swap" rel="stylesheet">
<style>
  :root {
    --page-bg: #e4e2df;
    --card-dark: #1b1c1e;
    --card-blue: #0f77c0;
    --accent-grey: #8a8b8d;
    --logo-blue: #1a78c3;
    --logo-cyan: #27def4;
    --text-white: #ffffff;
  }
  * { margin: 0; padding: 0; box-sizing: border-box; }
  html, body {
    width: 1125px;
    height: 1200px;
    overflow: hidden;
    background: var(--page-bg);
  }
  .sheet {
    position: relative;
    width: 1125px;
    height: 1200px;
  }
  .card {
    position: absolute;
    left: 150px;
    width: 825px;
    height: 470px;
    overflow: hidden;
    box-shadow: 0 2px 6px rgba(0,0,0,0.18);
  }
  .card--front { top: 98px; background: var(--card-dark); }
  .card--back { top: 632px; background: var(--card-blue); }

  .front-shapes {
    position: absolute;
    inset: 0;
    width: 100%;
    height: 100%;
  }
  .front-shapes .blue-panel { fill: var(--card-blue); }
  .front-shapes .divider { stroke: var(--accent-grey); stroke-width: 3; }

  .wordmark {
    position: absolute;
    font-family: "Roboto Condensed", sans-serif;
    font-weight: 500;
    white-space: nowrap;
    line-height: 1;
  }
  .wordmark--front {
    left: 93px;
    top: 162px;
    font-size: 48px;
    color: var(--logo-blue);
    letter-spacing: 1px;
  }
  .wordmark--back {
    left: 0;
    right: 0;
    top: 205px;
    text-align: center;
    font-size: 56px;
    color: var(--logo-cyan);
    letter-spacing: 1px;
  }

  .contact-block {
    position: absolute;
    right: 49px;
    top: 244px;
    color: var(--text-white);
    text-align: right;
  }
  .person-name {
    font-family: "Exo 2", sans-serif;
    font-weight: 600;
    font-size: 26px;
    letter-spacing: 0.5px;
    line-height: 30px;
  }
  .person-title {
    font-family: "Roboto", sans-serif;
    font-weight: 700;
    font-size: 17px;
    line-height: 22px;
    margin-bottom: 20px;
  }
  .contact-list { list-style: none; }
  .contact-item {
    display: flex;
    justify-content: flex-end;
    align-items: center;
    gap: 12px;
    font-family: "Roboto", sans-serif;
    font-size: 17px;
    line-height: 24px;
  }
  .contact-icon {
    width: 15px;
    height: 15px;
    flex: none;
  }
</style>
</head>
<body>
<main class="sheet">
  <section class="card card--front" aria-label="Business card, details side">
    <svg class="front-shapes" viewBox="0 0 825 470" preserveAspectRatio="none" aria-hidden="true">
      <polygon class="blue-panel" points="702,0 825,0 825,470 339,470"/>
      <line class="divider" x1="693" y1="2" x2="325" y2="470"/>
    </svg>

    <div class="wordmark wordmark--front">RW Framewell</div>

    <div class="contact-block">
      <p class="person-name">DANIEL HART</p>
      <p class="person-title">President</p>
      <ul class="contact-list">
        <li class="contact-item">555-204-7731
          <svg class="contact-icon" viewBox="0 0 16 16" aria-hidden="true"><path fill="#fff" d="M3.6 1.2l2.3 2.6-1.3 1.8c.9 2.2 2.6 3.9 4.8 4.8l1.8-1.3 2.6 2.3-1.2 2.2C7.4 15.4.6 8.6 1.4 2.4z"/></svg>
        </li>
        <li class="contact-item">555-318-6642
          <svg class="contact-icon" viewBox="0 0 16 16" aria-hidden="true"><rect x="4" y="1" width="8" height="14" rx="1.5" fill="none" stroke="#fff" stroke-width="1.6"/><circle cx="8" cy="12.5" r="0.9" fill="#fff"/></svg>
        </li>
        <li class="contact-item">info@rwframewell.com
          <svg class="contact-icon" viewBox="0 0 16 16" aria-hidden="true"><rect x="1" y="4" width="14" height="9" fill="#fff"/><path d="M1.5 4.5L8 9.5l6.5-5" fill="none" stroke="#0f77c0" stroke-width="1.3"/></svg>
        </li>
        <li class="contact-item">www.rwframewell.com
          <svg class="contact-icon" viewBox="0 0 16 16" aria-hidden="true"><circle cx="8" cy="8" r="7" fill="#fff"/><path d="M5 4.5c1.5.5 2 1.8 1.2 2.8S7 10 6 11.5M10.5 3.5c-.6 1.4.2 2.4 1.6 2.6M11 10c-1 .3-1.4 1.3-1 2.5" fill="none" stroke="#0f77c0" stroke-width="1.3"/></svg>
        </li>
      </ul>
    </div>
  </section>

  <section class="card card--back" aria-label="Business card, logo side">
    <div class="wordmark wordmark--back">RW Framewell</div>
  </section>
</main>
</body>
</html>
```